Doctor Formulated Medical Cosmetics

Velour Skinhaus is an E-commerce site for high end Medical Cosmetics designed to treat specific skin problems. The Velour Skinhaus difference/advantage is that all creams and serums are:
Doctor Formulated, Freshly Handmade, Registered Pharmacy.
The Site also provides real doctor Dermatology Consultations, Library (with a list of - 1. Active Ingredients in the creams with description of their effects, 2. Skin Conditions with information on what causes the condition and typical treatment approaches and outcomes. 3. Resources from Dermatology Journals and literature on the conditions.)
Header Information: Velour Skinhaus, languages EN, BG, Register / log in, Shopping Bag. This field should be narrow.
Categories (horizontal): Home, Face, Body, Hair Care, Skin Conditions, Doctor Consultation, Library
The Landing Page should have only one well organized picture, which is intended to create the feeling of luxury, freedom and relaxation. It will be large and will fill the whole screen. All text should be on transparent or similar color fields. Please use the color of the text to create also the feeling of conservative luxury.
Written message / image overlay Velour Skinhaus(logo), Skin Care, Doctor Formulated, Freshly Handmade, Registered Pharmacy.
Please study the Landing Page of this site as an example: www.marivane.com
Under the Landing Page, there should be a slider with 4 of our products.
Underneath: Four Blog Articles (large pictures for maximum impact and luxury text underneath).
Underneath: Banner for Dermatologist Consultation, (button for Start Your Case Now).
Underneath: Two pictures in a line - Library (with books), and Active Ingredients.
Footer: Philosophy, Categories, Customer Care
Please adhere to the color palate provided in the pictures (as attachments). Provided are some examples of Web Sites with the desired look and feel. www.quillora.com , www.tavenholtmd.com .
Please use different shades of gray, white, beige and gold colors, and black. Our products will be in brown glass jars and bottles to convey the professional, pharmacy made nature of the creams and lotions.
We find the following Front Page very attractive and effective - www.marivane.com , with its full page image and overlaying text.
Please have a look at this link for the Landing page.
http://www.brimlensphoto.com/detail/video/woman-lying-on-a-black-sand-beach-in-a-bikini-stock-footage/58213067
I would like to use it in the animated version to achieve the WOW effect. I have uploaded the jpeg version for it, so you will be able create your design.
For the Landing page design, please use only the two uploaded pictures of a woman laying at the beach. Let's see how each of them will look like.
Thank you for your help.

```html
<!DOCTYPE html>
<html lang="en">
<head>
<meta charset="utf-8">
<title>Velour Skinhaus — Doctor Formulated Medical Cosmetics</title>
<link href="https://fonts.googleapis.com/css2?family=Open+Sans:wght@400;600;700&display=swap" rel="stylesheet">
<style>
  :root{
    --gold:#d4b46c;
    --gold-deep:#c9a558;
    --beige:#f6f2de;
    --ink:#2c2c2c;
    --ink-soft:#555;
    --muted:#8a8a8a;
    --line:#dcdcdc;
    --white:#ffffff;
    --night:#1d1d1d;
  }
  *{box-sizing:border-box;margin:0;padding:0}
  html,body{width:1200px;height:2442px;overflow:hidden;background:var(--white)}
  body{position:relative;font-family:"Open Sans",Arial,sans-serif;color:var(--ink)}
  .abs{position:absolute}

  /* header */
  .site-header{position:absolute;left:0;top:0;width:1200px;height:94px;background:var(--white)}
  .brand{position:absolute;display:flex;align-items:center;gap:10px;font-weight:400;color:var(--gold);white-space:nowrap}
  .brand .mark{border:2px solid var(--gold);border-radius:50%}
  .header-brand{left:98px;top:26px;font-size:34px}
  .header-brand .mark{width:40px;height:40px}
  .utility{position:absolute;top:38px;font-size:13px;color:var(--ink);display:flex;align-items:center;gap:6px;white-space:nowrap}
  .utility svg{display:block}
  .sep{position:absolute;top:36px;font-size:14px;color:var(--ink)}
  .bag{position:absolute;left:1081px;top:30px}

  /* nav */
  .main-nav{position:absolute;left:0;top:94px;width:1200px;height:46px;background:var(--gold)}
  .main-nav a{position:absolute;top:13px;font-size:15px;font-weight:600;color:var(--white);text-decoration:none;white-space:nowrap}
  .search{position:absolute;left:869px;top:7px;width:231px;height:33px;border:1.5px solid var(--white);color:var(--white);font-size:13px;padding:7px 12px}
  .search svg{position:absolute;right:10px;top:9px}

  /* hero */
  .hero{position:absolute;left:0;top:140px;width:1200px;height:475px;overflow:hidden;background:var(--night)}
  .hero-photo{position:absolute;left:0;top:0;width:1200px;height:475px;
    background:linear-gradient(100deg,#6e6a66 0%,#9a8b78 22%,#c2a783 38%,#8a7b6c 55%,#3a3838 68%,#222 80%,#1b1b1b 100%)}
  .hero-panel{position:absolute;left:790px;top:0;width:330px;height:475px;color:var(--white)}
  .hero-brand{position:absolute;left:0;top:52px;display:flex;align-items:center;gap:14px;font-size:36px;color:var(--white);white-space:nowrap}
  .hero-brand .mark{width:106px;height:106px;border:2px solid var(--white);border-radius:50%}
  .hero-rule{position:absolute;left:0;top:182px;width:310px;height:2px;background:#9a9a9a}
  .benefits{position:absolute;left:16px;top:206px;list-style:none}
  .benefits li{display:flex;align-items:center;gap:13px;height:33.6px;font-size:17px;color:#f2f2f2}
  .btn-gold{position:absolute;background:var(--gold);color:var(--white);font-weight:700;text-align:center;letter-spacing:.3px}
  .hero .btn-gold{left:14px;top:355px;width:140px;height:36px;line-height:36px;font-size:14px}
  .dots{position:absolute;left:572px;top:410px;display:flex;gap:5px}
  .dots span{width:15px;height:15px;border-radius:50%;border:2px solid var(--white)}
  .dots span.on{background:var(--white)}

  /* section titles */
  .section-title{position:absolute;left:0;width:1200px;text-align:center;font-size:25px;font-weight:600;color:var(--ink)}

  /* products */
  .divider{position:absolute;left:440px;top:710px;width:320px;height:38px}
  .product-card{position:absolute;top:785px;width:234px;height:270px;border:1.5px solid var(--line);background:var(--white)}
  .product-shot{position:absolute;left:68px;top:14px;width:98px;height:240px;border-radius:10px 10px 4px 4px;
    background:linear-gradient(180deg,#2a2a2a 0%,#2a2a2a 10%,#e7b52a 14%,#f2c433 45%,#d8a31c 100%)}
  .product-name{position:absolute;top:1068px;width:234px;text-align:center;font-size:15px;font-weight:600;color:var(--ink)}
  .slider-arrow{position:absolute;top:908px}

  /* blog */
  .blog{position:absolute;left:0;top:1141px;width:1200px;height:384px;background:var(--beige)}
  .teaser{position:absolute;width:330px;height:98px}
  .teaser-photo{position:absolute;left:0;top:0;width:117px;height:98px}
  .teaser-text{position:absolute;left:130px;top:0;font-size:13.5px;font-weight:600;line-height:19.5px;color:var(--ink)}
  .teaser-date{position:absolute;left:130px;top:62px;display:flex;align-items:center;gap:6px;font-size:13.5px;color:var(--gold-deep)}

  /* consultation */
  .consult{position:absolute;left:0;top:1525px;width:1200px;height:325px;
    background:linear-gradient(90deg,#7c7c7c 0%,#9b9b9b 35%,#b9b4ae 60%,#d8c4b4 78%,#cdbdb2 100%)}
  .consult h2{position:absolute;left:98px;top:64px;font-size:38px;font-weight:600;color:var(--white);white-space:nowrap}
  .consult p{position:absolute;left:98px;top:122px;width:540px;font-size:13.5px;line-height:25px;color:#f4f4f4}
  .consult .btn-gold{left:98px;top:212px;width:115px;height:36px;line-height:36px;font-size:12px}

  /* footer */
  .site-footer{position:absolute;left:0;top:2110px;width:1200px;height:264px;background:var(--beige)}
  .footer-brand{left:98px;top:106px;font-size:34px}
  .footer-brand .mark{width:40px;height:40px}
  .footer-col{position:absolute;top:46px}
  .footer-col h3{font-size:16px;font-weight:600;color:var(--ink);margin-bottom:12px}
  .footer-col ul{list-style:none}
  .footer-col li{font-size:12px;color:var(--ink-soft);height:30px}
  .news-note{position:absolute;left:791px;top:76px;width:300px;font-size:12px;line-height:18px;color:var(--ink-soft)}
  .news-field{position:absolute;left:791px;top:119px;width:309px;height:37px;background:var(--white);border:1px solid #e6e0c8;font-size:12.5px;color:var(--ink);padding:10px 14px}
  .news-btn{position:absolute;left:1016px;top:119px;width:84px;height:37px;line-height:37px;background:var(--gold);color:var(--white);font-size:13px;font-weight:700;text-align:center}
  .stay{position:absolute;left:791px;top:168px;font-size:16px;font-weight:600;color:var(--ink)}
  .socials{position:absolute;left:791px;top:203px;display:flex;gap:30px}
  .socials span{width:16px;height:16px;border-radius:50%;background:#9a9a9a}
  .base-bar{position:absolute;left:0;top:2374px;width:1200px;height:68px;background:var(--gold)}
  .base-bar small{position:absolute;left:98px;top:25px;font-size:12px;color:var(--white)}
  .cards{position:absolute;left:889px;top:20px;display:flex;gap:4px}
  .cards span{width:50px;height:30px;border-radius:3px}
</style>
</head>
<body>

<header class="site-header">
  <div class="brand header-brand"><span class="mark"></span>Velour Skinhaus</div>

  <div class="utility" style="left:571px">
    <svg width="18" height="12" viewBox="0 0 18 12"><rect width="18" height="12" fill="#1f3f8f"/><rect x="7" width="4" height="12" fill="#fff"/><rect y="4" width="18" height="4" fill="#fff"/><rect x="8" width="2" height="12" fill="#c8102e"/><rect y="5" width="18" height="2" fill="#c8102e"/></svg>EN
  </div>
  <span class="sep" style="left:627px">|</span>
  <div class="utility" style="left:643px">
    <svg width="18" height="12" viewBox="0 0 18 12"><rect width="18" height="4" fill="#fff" stroke="#ddd" stroke-width=".5"/><rect y="4" width="18" height="4" fill="#00966e"/><rect y="8" width="18" height="4" fill="#d62612"/></svg>BG
  </div>
  <div class="utility" style="left:711px">
    <svg width="12" height="14" viewBox="0 0 12 14"><circle cx="6" cy="4" r="3.2" fill="#333"/><path d="M0 14c0-4 2.6-6 6-6s6 2 6 6z" fill="#333"/></svg>Doctor
  </div>
  <span class="sep" style="left:790px">|</span>
  <div class="utility" style="left:811px">
    <svg width="15" height="13" viewBox="0 0 15 13"><rect x="0" y="3" width="15" height="10" rx="1.5" fill="#333"/><rect x="5" y="0.5" width="5" height="3" rx="1" fill="none" stroke="#333" stroke-width="1.4"/></svg>Pharmacy
  </div>
  <span class="sep" style="left:914px">|</span>
  <div class="utility" style="left:931px">
    <svg width="12" height="14" viewBox="0 0 12 14"><circle cx="6" cy="4" r="3.2" fill="#333"/><path d="M0 14c0-4 2.6-6 6-6s6 2 6 6z" fill="#333"/></svg>Register / log in
  </div>
  <svg class="bag" width="22" height="30" viewBox="0 0 22 30"><path d="M6 10V6a5 5 0 0 1 10 0v4" fill="none" stroke="#d4b46c" stroke-width="2"/><rect x="0" y="10" width="22" height="20" rx="2" fill="#d4b46c"/></svg>
</header>

<nav class="main-nav">
  <a style="left:98px">Face</a>
  <a style="left:177px">Body</a>
  <a style="left:257px">Hair Care</a>
  <a style="left:371px">Skin Concerns</a>
  <a style="left:521px">Dermatologist Consultation</a>
  <a style="left:770px">Library</a>
  <div class="search">Search
    <svg width="14" height="14" viewBox="0 0 14 14"><circle cx="6" cy="6" r="4.5" fill="none" stroke="#fff" stroke-width="2"/><path d="M9.5 9.5L13 13" stroke="#fff" stroke-width="2"/></svg>
  </div>
</nav>

<section class="hero">
  <div class="hero-photo" role="img" aria-label="Large photograph of a relaxed woman with long blonde hair against a dark backdrop"></div>
  <div class="hero-panel">
    <div class="hero-brand"><span class="mark"></span>Velour<br>Skinhaus</div>
    <div class="hero-rule"></div>
    <ul class="benefits">
      <li><svg width="16" height="16" viewBox="0 0 16 16"><circle cx="8" cy="8" r="8" fill="#d4b46c"/><path d="M4.3 8.2l2.5 2.5 4.9-5" fill="none" stroke="#1d1d1d" stroke-width="2"/></svg>Doctor Formulated</li>
      <li><svg width="16" height="16" viewBox="0 0 16 16"><circle cx="8" cy="8" r="8" fill="#d4b46c"/><path d="M4.3 8.2l2.5 2.5 4.9-5" fill="none" stroke="#1d1d1d" stroke-width="2"/></svg>Freshly Handmade</li>
      <li><svg width="16" height="16" viewBox="0 0 16 16"><circle cx="8" cy="8" r="8" fill="#d4b46c"/><path d="M4.3 8.2l2.5 2.5 4.9-5" fill="none" stroke="#1d1d1d" stroke-width="2"/></svg>Registered Pharmacy</li>
      <li><svg width="16" height="16" viewBox="0 0 16 16"><circle cx="8" cy="8" r="8" fill="#d4b46c"/><path d="M4.3 8.2l2.5 2.5 4.9-5" fill="none" stroke="#1d1d1d" stroke-width="2"/></svg>Highest Ethical Standards</li>
    </ul>
    <div class="btn-gold">SHOP NOW!</div>
  </div>
  <div class="dots"><span class="on"></span><span></span><span></span></div>
</section>

<h2 class="section-title" style="top:662px">Our Products</h2>
<svg class="divider" viewBox="0 0 320 38"><line x1="0" y1="19" x2="140" y2="19" stroke="#d8d8d8"/><line x1="180" y1="19" x2="320" y2="19" stroke="#d8d8d8"/><circle cx="160" cy="19" r="18" fill="none" stroke="#e2d2a8" stroke-width="2"/></svg>

<svg class="slider-arrow" style="left:66px" width="14" height="24" viewBox="0 0 14 24"><path d="M12 2L2 12l10 10" fill="none" stroke="#aaa" stroke-width="2"/></svg>
<svg class="slider-arrow" style="left:1120px" width="14" height="24" viewBox="0 0 14 24"><path d="M2 2l10 10L2 22" fill="none" stroke="#aaa" stroke-width="2"/></svg>

<div class="product-card" style="left:98px"><div class="product-shot" role="img" aria-label="Amber glass bottle of Doctor Formulated serum"></div></div>
<div class="product-card" style="left:355px"><div class="product-shot" role="img" aria-label="Amber glass bottle of Freshly Handmade serum"></div></div>
<div class="product-card" style="left:611px"><div class="product-shot" role="img" aria-label="Amber glass bottle of Registered Pharmacy serum"></div></div>
<div class="product-card" style="left:867px"><div class="product-shot" role="img" aria-label="Amber glass bottle of Highest Ethical Standards serum"></div></div>
<div class="product-name" style="left:98px">Doctor Formulated</div>
<div class="product-name" style="left:355px">Freshly Handmade</div>
<div class="product-name" style="left:611px">Registered Pharmacy</div>
<div class="product-name" style="left:867px">Highest Ethical Standards</div>

<section class="blog">
  <h2 class="section-title" style="top:42px">Blog Articles</h2>

  <article class="teaser" style="left:98px;top:111px">
    <div class="teaser-photo" role="img" aria-label="Woman holding a like sign" style="background:linear-gradient(135deg,#c98d84,#8e3b3b)"></div>
    <div class="teaser-text">At vero eos et accusamus et<br>iusto odio dignissimos ducim<br>us quiblandit</div>
    <div class="teaser-date"><svg width="12" height="12" viewBox="0 0 12 12"><rect x="0.5" y="2" width="11" height="9.5" fill="#c9a558"/><rect x="2" y="0" width="2" height="3" fill="#c9a558"/><rect x="8" y="0" width="2" height="3" fill="#c9a558"/></svg>31/08/2016</div>
  </article>
  <article class="teaser" style="left:438px;top:111px">
    <div class="teaser-photo" role="img" aria-label="Woman with flowing hair" style="background:linear-gradient(135deg,#f1ede8,#c9a688)"></div>
    <div class="teaser-text">At vero eos et accusamus et<br>iusto odio dignissimos ducim<br>us quiblandit</div>
    <div class="teaser-date"><svg width="12" height="12" viewBox="0 0 12 12"><rect x="0.5" y="2" width="11" height="9.5" fill="#c9a558"/><rect x="2" y="0" width="2" height="3" fill="#c9a558"/><rect x="8" y="0" width="2" height="3" fill="#c9a558"/></svg>31/08/2016</div>
  </article>
  <article class="teaser" style="left:783px;top:111px">
    <div class="teaser-photo" role="img" aria-label="White flowers beside a cream jar" style="background:linear-gradient(135deg,#7a8a6a,#e8e6e0)"></div>
    <div class="teaser-text">At vero eos et accusamus et<br>iusto odio dignissimos ducim<br>us quiblandit</div>
    <div class="teaser-date"><svg width="12" height="12" viewBox="0 0 12 12"><rect x="0.5" y="2" width="11" height="9.5" fill="#c9a558"/><rect x="2" y="0" width="2" height="3" fill="#c9a558"/><rect x="8" y="0" width="2" height="3" fill="#c9a558"/></svg>31/08/2016</div>
  </article>

  <article class="teaser" style="left:98px;top:241px">
    <div class="teaser-photo" role="img" aria-label="Woman touching her skin" style="background:linear-gradient(135deg,#9fb4c4,#e5e1dc)"></div>
    <div class="teaser-text">At vero eos et accusamus et<br>iusto odio dignissimos ducim<br>us quiblandit</div>
    <div class="teaser-date"><svg width="12" height="12" viewBox="0 0 12 12"><rect x="0.5" y="2" width="11" height="9.5" fill="#c9a558"/><rect x="2" y="0" width="2" height="3" fill="#c9a558"/><rect x="8" y="0" width="2" height="3" fill="#c9a558"/></svg>31/08/2016</div>
  </article>
  <article class="teaser" style="left:438px;top:241px">
    <div class="teaser-photo" role="img" aria-label="Cream jars and candles" style="background:linear-gradient(135deg,#e6d6bf,#b08a62)"></div>
    <div class="teaser-text">At vero eos et accusamus et<br>iusto odio dignissimos ducim<br>us quiblandit</div>
    <div class="teaser-date"><svg width="12" height="12" viewBox="0 0 12 12"><rect x="0.5" y="2" width="11" height="9.5" fill="#c9a558"/><rect x="2" y="0" width="2" height="3" fill="#c9a558"/><rect x="8" y="0" width="2" height="3" fill="#c9a558"/></svg>31/08/2016</div>
  </article>
  <article class="teaser" style="left:783px;top:241px">
    <div class="teaser-photo" role="img" aria-label="Scientist working in a laboratory" style="background:linear-gradient(135deg,#2d5b85,#cfdbe6)"></div>
    <div class="teaser-text">At vero eos et accusamus et<br>iusto odio dignissimos ducim<br>us quiblandit</div>
    <div class="teaser-date"><svg width="12" height="12" viewBox="0 0 12 12"><rect x="0.5" y="2" width="11" height="9.5" fill="#c9a558"/><rect x="2" y="0" width="2" height="3" fill="#c9a558"/><rect x="8" y="0" width="2" height="3" fill="#c9a558"/></svg>31/08/2016</div>
  </article>
</section>

<section class="consult" role="img" aria-label="Soft grey photograph of a woman's face beside a molecule model">
  <h2>Dermatologist Consultation</h2>
  <p>Nam libero tempore, cum soluta nobis est eligendi optio cumque nihil impediquo minus id quod maxime placeat facere possimus, omnis voluptas assumenda estet omnis dolor repellendusoribus autem quibusdam.</p>
  <div class="btn-gold">READ MORE &gt;&gt;</div>
</section>

<h2 class="section-title" style="top:1893px">News Articles</h2>

<article class="teaser" style="left:98px;top:1958px">
  <div class="teaser-photo" role="img" aria-label="Skin treatment at a clinic" style="background:linear-gradient(135deg,#e9e6e3,#b88a74)"></div>
  <div class="teaser-text">At vero eos et accusamus et<br>iusto odio dignissimos ducim<br>us quiblandit</div>
  <div class="teaser-date"><svg width="12" height="12" viewBox="0 0 12 12"><rect x="0.5" y="2" width="11" height="9.5" fill="#c9a558"/><rect x="2" y="0" width="2" height="3" fill="#c9a558"/><rect x="8" y="0" width="2" height="3" fill="#c9a558"/></svg>31/08/2016</div>
</article>
<article class="teaser" style="left:438px;top:1958px">
  <div class="teaser-photo" role="img" aria-label="Woman with a facial mask" style="background:linear-gradient(135deg,#f2ece6,#d6a98e)"></div>
  <div class="teaser-text">At vero eos et accusamus et<br>iusto odio dignissimos ducim<br>us quiblandit</div>
  <div class="teaser-date"><svg width="12" height="12" viewBox="0 0 12 12"><rect x="0.5" y="2" width="11" height="9.5" fill="#c9a558"/><rect x="2" y="0" width="2" height="3" fill="#c9a558"/><rect x="8" y="0" width="2" height="3" fill="#c9a558"/></svg>31/08/2016</div>
</article>
<article class="teaser" style="left:783px;top:1958px">
  <div class="teaser-photo" role="img" aria-label="Women shopping for skincare in a store" style="background:linear-gradient(135deg,#8a6a4e,#e7ddd0)"></div>
  <div class="teaser-text">At vero eos et accusamus et<br>iusto odio dignissimos ducim<br>us quiblandit</div>
  <div class="teaser-date"><svg width="12" height="12" viewBox="0 0 12 12"><rect x="0.5" y="2" width="11" height="9.5" fill="#c9a558"/><rect x="2" y="0" width="2" height="3" fill="#c9a558"/><rect x="8" y="0" width="2" height="3" fill="#c9a558"/></svg>31/08/2016</div>
</article>

<footer class="site-footer">
  <div class="brand footer-brand"><span class="mark"></span>Velour Skinhaus</div>

  <div class="footer-col" style="left:397px">
    <h3>Information</h3>
    <ul><li>Store Locator</li><li>Privacy Policy</li><li>Terms Of Use</li><li>Security Policy</li><li>Affiliate Program</li></ul>
  </div>
  <div class="footer-col" style="left:576px">
    <h3>Customer Service</h3>
    <ul><li>FAQ</li><li>Shipping Information</li><li>Returns and Exchanges</li><li>Auto Delivery Service</li><li>Complimentary Services</li></ul>
  </div>
  <div class="footer-col" style="left:791px"><h3>Sign up for Newsletter</h3></div>
  <div class="news-note">Register your email address to get information about us</div>
  <div class="news-field">Email Address</div>
  <div class="news-btn">SIGN UP</div>
  <div class="stay">Stay Connected</div>
  <div class="socials"><span></span><span></span><span></span><span></span><span></span></div>
</footer>

<div class="base-bar">
  <small>Copyrights © 2016, Velour Skinhaus | All rights reserved</small>
  <div class="cards">
    <span style="background:#e6e6e6"></span>
    <span style="background:#f4f4f4"></span>
    <span style="background:#ececec"></span>
    <span style="background:#5a86b8"></span>
  </div>
</div>

</body>
</html>
```